Design a sleek menu for our new smoothie and snacks shop”Glee”

requiring a store drinks and snacks menu we would like to have a white background for the menu . I would like to have fruit watermarks like in our original design concept , For reference ,please refer to the pictures . The font and layout of the menu should be modern , simple but stylish and reflect a smoothie shop.
we will be proving the menu contents to input once we agree to the design concept .
here are the menu documents

smoothies

Regular 16oz £4.99 Large 20oz £5.99
substitute semi skim for any dairy free milks for .50p
add vegan protein or regular protein for .50p

Berry set go
mixed berries, banana, coconut yogurt, milk

Green Machine
Spinach, avocado, matcha, banana, milk, agave

Power to the purple
Blueberries, banana, açai, coconut milk

Mango Monsoon
Mango, apple, strawberry, coconut milk, vanilla yogurt, agave

Go Ape Glee
Oats, banana, cinnamon, dates, almond butter

Caribbean Dream
Pineapple, spinach, banana, coconut milk

Mocha lotta
Oats, banana, cinnamon, cocoa, espresso, skim milk

Cocoa Banana
Oats, banana, cocoa, cinnamon, peanut butter , agave
*almond butter substitute is available

PB & J Day
Frozen berries, banana, peanut butter, maple syrup, coconut milk
*Spinach is optional

Strawberry Glee
Strawberries, banana, coconut milk, orange juice, agave

Kale Krush
Spinach, kale, pineapple, apple juice

Young Blood
Celery, lemon, apple

Berry Beautiful
Blueberries, banana, vanilla yogurt, soy milk, collagen protein, agave,

Shakes
Large 16oz £6
Add Protein for .50p

Avo Shake
Avocado, banana, skim milk, vanilla

Cocoa Shake
Avocado, cocoa powder, coconut milk, banana, maple syrup
*can substitute avocado with dairy free ice cream

Sweet Vegan
Dairy free vanilla Ice cream, banana, cocoa powder, coconut milk, agave

The last straw
Strawberry ,dates , dairy free ice cream, coconut milk, agave
*substitute dairy free ice cream for avocado

Caffeine frenzy
Espresso, banana, dairy free ice cream, cocoa powder, almond milk, agave

Berry Bunch
Oats, mixed berries, banana, dates ,soy milk, dairy free ice cream

Immune boosters
Regular 16 oz £6
Smoothie Bowl £5.50 * Available on a seasonal basis

The yellow one: Pineapple turmeric
Pineapple, banana, lemon, agave, ginger,tumeric,coconut water

The Red one : Citrus Berry Ginger
Orange, strawberry, lemon, ginger , almond milk

The Orange one : Citrus carrot
Grapefruit, clementine, carrot,mango,yogurt,lemon,tumeric

Teas
Regular £2
Green geisha
Breakfast blend
Lemon & ginger
Moroccan mint

Iced Frappucino
* Substitute for non dairy for .50p
Regular £3.50
Cappuccino - expresso, milk, ice
Mocha- cocoa ,milk, ice
Strawberry's n cream- Strawberry,cream,ice
Mighty Matcha - Matcha, cream, ice
Vanilla Bean- Vanilla, cream, ice
Glee Sandwiches
£4.50

Avocado
Avocado , mozerella,tomatoe, pesto

Spicy Tuna
Tuna, Chilli peppers, mayo, salt, pepper

Tunacado
Tuna, avocado, mayo, salt, pepper

BLT
Turkey Rasher, lettuce, mayo, tomatoe

American Grilled Cheese
Mature Cheddar , wholewheat bread
*sourdough bread is optional

Yogurt
£3
Coconut ,Vanilla yogurt , banana, granola

Bowls
£4.50
+ protein=.50p

Acai Bowl
Acai, Raspberry,blueberry,banana,almond milk, granola
*Topping: granola and ½ banana sliced ,chia seeds

Cocoa Bowl
Cocoa,banana,peanut butter,almond milk
Toppings : chocolate granola, peanut butter ,chia seeds,1/2 banana sliced

Target Market(s)

any age , predominately ages 20+

Industry/Entity Type

food & drink

Colors

Designer to choose colors to be used in the design.

Requirements
Must have
• clean, modern concept
Nice to have
• white background, fruits in the background -animated or actual ones
Should not have
• no dark background concepts

```html
<!DOCTYPE html>
<html lang="en">
<head>
<meta charset="utf-8">
<title>Glee – Menu Board &amp; Shopfront</title>
<link href="https://fonts.googleapis.com/css2?family=Oswald:wght@300;400;500&family=Roboto+Condensed:wght@400;700&display=swap" rel="stylesheet">
<style>
:root{
  --lime:#c3f36e;
  --navy:#22253f;
  --ink:#2b2d3a;
  --accent:#e0245e;
  --paper:#ffffff;
  --stage:#eeeeec;
  --slat:#e4e2dd;
  --slat-line:#c9c6bf;
}
*{margin:0;padding:0;box-sizing:border-box}
html,body{width:1200px;height:891px;overflow:hidden;background:var(--stage)}
body{position:relative;font-family:"Roboto Condensed",sans-serif;color:var(--ink)}

/* ---------- menu board ---------- */
.menu-board{position:absolute;left:24px;top:14px;width:500px;height:863px;background:var(--paper);box-shadow:0 2px 10px rgba(0,0,0,.12)}
.fruit-border{position:absolute;inset:0;background:radial-gradient(circle at 20% 10%,#f3f3f3,#fff 40%),linear-gradient(#fafafa,#f0f0f0)}
.menu-panel{position:absolute;left:18px;top:16px;right:18px;bottom:24px;background:linear-gradient(160deg,#cbf57c,var(--lime) 55%,#b9ec62);display:flex;gap:14px;padding:26px 10px 14px 0}
.menu-tag{position:absolute;left:50%;top:0;transform:translateX(-50%);width:40px;height:50px;background:var(--navy);display:flex;align-items:center;justify-content:center}
.menu-tag span{color:#fff;font-family:"Oswald",sans-serif;font-weight:400;font-size:13px}
.menu-col{flex:1;display:flex;flex-direction:column;justify-content:space-between}
.menu-col--right{text-align:right;border-left:1px dashed rgba(34,37,63,.35);padding-left:10px}
.block{display:flex;flex-direction:column}
.section-title{font-family:"Oswald",sans-serif;font-weight:300;font-size:17px;color:var(--navy);text-transform:uppercase;letter-spacing:.2px;line-height:1.1}
.menu-col--left .section-title{padding-left:14px}
.price-bar{background:var(--navy);color:#fff;font-size:7.4px;line-height:1.2;padding:3px 6px 3px 14px;margin:2px 0 6px;text-transform:uppercase}
.menu-col--right .price-bar{padding:3px 6px;margin-left:auto;display:inline-block;align-self:flex-end}
.item{margin:0 0 7px;padding-left:14px;line-height:1.1}
.menu-col--right .item{padding-left:0;margin-bottom:4px}
.item-name{font-family:"Oswald",sans-serif;font-weight:400;font-size:8.4px;text-transform:uppercase;color:var(--navy)}
.item-desc{font-size:7.4px;color:var(--ink)}
.item-note{font-size:7.4px;color:var(--accent)}
.rule{border-top:1px dashed rgba(34,37,63,.35);margin:4px 0 2px}

/* ---------- shopfront signage ---------- */
.fascia{position:absolute;left:560px;top:120px;width:620px;height:104px;background:var(--lime);display:flex;align-items:center;justify-content:center;gap:14px}
.fascia-dot{width:46px;height:46px;border-radius:50%;background:var(--navy)}
.fascia-name{font-family:"Oswald",sans-serif;font-weight:400;font-size:44px;color:var(--navy)}
.shutter{position:absolute;left:570px;top:224px;width:600px;height:653px;background:repeating-linear-gradient(var(--slat) 0 9px,var(--slat-line) 9px 10px);display:flex;flex-direction:column;align-items:center;justify-content:center}
.shutter-brand{display:flex;align-items:center;gap:18px}
.shutter-dot{width:40px;height:40px;border-radius:50%;background:var(--navy)}
.shutter-name{font-family:"Oswald",sans-serif;font-weight:400;font-size:150px;line-height:1;color:var(--navy)}
.tagline{font-family:"Oswald",sans-serif;font-weight:400;font-size:26px;color:var(--navy);letter-spacing:1px;text-align:center;line-height:1.2;margin-top:24px}
</style>
</head>
<body>

<section class="menu-board" aria-label="Glee drinks and snacks menu">
  <div class="fruit-border" role="img" aria-label="Hand-sketched fruit pattern border in grey and white"></div>
  <div class="menu-panel">
    <div class="menu-tag"><span>Glee</span></div>

    <div class="menu-col menu-col--left">
      <div class="block">
        <h2 class="section-title">Smoothies</h2>
        <div class="price-bar">Regular 16oz £4.99 Large 20oz £5.99<br>Substitute semi skim for any dairy free milks for .50p<br>Add vegan protein or regular protein for .50p</div>
        <div class="item"><div class="item-name">Berry Set Go</div><div class="item-desc">Mixed berries, banana, coconut yogurt, milk</div></div>
        <div class="item"><div class="item-name">Green Machine</div><div class="item-desc">Spinach, avocado, matcha, banana, milk, agave</div></div>
        <div class="item"><div class="item-name">Power to the Purple</div><div class="item-desc">Blueberries, banana, açai, coconut milk</div></div>
        <div class="item"><div class="item-name">Mango Monsoon</div><div class="item-desc">Mango, apple, strawberry, coconut milk,<br>vanilla yogurt, agave</div></div>
        <div class="item"><div class="item-name">Go Ape Glee</div><div class="item-desc">Oats, banana, cinnamon, dates, almond butter</div></div>
        <div class="item"><div class="item-name">Caribbean Dream</div><div class="item-desc">Pineapple, spinach, banana, coconut milk</div></div>
        <div class="item"><div class="item-name">Mocha Lotta</div><div class="item-desc">Oats, banana, cinnamon, cocoa,<br>espresso, skim milk</div></div>
        <div class="item"><div class="item-name">Cocoa Banana</div><div class="item-desc">Oats, banana, cocoa, cinnamon,<br>peanut butter, agave</div><div class="item-note">*almond butter substitute is available</div></div>
        <div class="item"><div class="item-name">PB &amp; J Day</div><div class="item-desc">Frozen berries, banana, peanut butter,<br>maple syrup, coconut milk<br>*Spinach is optional</div></div>
        <div class="item"><div class="item-name">Strawberry Glee</div><div class="item-desc">Strawberries, banana, coconut milk,<br>orange juice, agave</div></div>
        <div class="item"><div class="item-name">Kale Krush</div><div class="item-desc">Spinach, kale, pineapple, apple juice</div></div>
        <div class="item"><div class="item-name">Young Blood</div><div class="item-desc">Celery, lemon, apple</div></div>
        <div class="item"><div class="item-name">Berry Beautiful</div><div class="item-desc">Blueberries, banana, vanilla yogurt, soy milk,<br>collagen protein, agave</div></div>
      </div>

      <div class="block">
        <h2 class="section-title">Shakes</h2>
        <div class="price-bar">Large 16oz £6<br>Add Protein for .50p</div>
        <div class="item"><div class="item-name">Avo Shake</div><div class="item-desc">Avocado, banana, skim milk, vanilla</div></div>
        <div class="item"><div class="item-name">Cocoa Shake</div><div class="item-desc">Avocado, cocoa powder, coconut milk,<br>banana, maple syrup</div><div class="item-note">*can substitute avocado with dairy free ice cream</div></div>
        <div class="item"><div class="item-name">Sweet Vegan</div><div class="item-desc">Dairy free vanilla ice cream, banana,<br>cocoa powder, coconut milk, agave</div></div>
        <div class="item"><div class="item-name">The Last Straw</div><div class="item-desc">Strawberry, dates, dairy free ice cream,<br>coconut milk, agave</div><div class="item-note">*substitute dairy free ice cream for avocado</div></div>
        <div class="item"><div class="item-name">Caffeine Frenzy</div><div class="item-desc">Espresso, banana, dairy free ice cream,<br>cocoa powder, almond milk, agave</div></div>
        <div class="item"><div class="item-name">Berry Bunch</div><div class="item-desc">Oats, mixed berries, banana, dates, soy milk,<br>dairy free ice cream</div></div>
      </div>
    </div>

    <div class="menu-col menu-col--right">
      <div class="block">
        <h2 class="section-title">Immune Boosters</h2>
        <div class="price-bar">Regular 16 oz £6<br>Smoothie Bowl £5.50<br>Available on a seasonal basis</div>
        <div class="item"><div class="item-name">The Yellow One: Pineapple Turmeric</div><div class="item-desc">Pineapple, banana, lemon, agave, ginger,<br>turmeric, coconut water</div></div>
        <div class="item"><div class="item-name">The Red One: Citrus Berry Ginger</div><div class="item-desc">Orange, strawberry, lemon, ginger,<br>almond milk</div></div>
        <div class="item"><div class="item-name">The Orange One: Citrus Carrot</div><div class="item-desc">Grapefruit, clementine, carrot, mango,<br>yogurt, lemon, turmeric</div></div>
      </div>
      <div class="rule"></div>

      <div class="block">
        <h2 class="section-title">Teas</h2>
        <div class="price-bar">Regular £2</div>
        <div class="item"><div class="item-name">Green Geisha</div></div>
        <div class="item"><div class="item-name">Breakfast Blend</div></div>
        <div class="item"><div class="item-name">Lemon &amp; Ginger</div></div>
        <div class="item"><div class="item-name">Moroccan Mint</div></div>
      </div>
      <div class="rule"></div>

      <div class="block">
        <h2 class="section-title">Iced Blends</h2>
        <div class="price-bar">Regular £3.50</div>
        <div class="item"><div class="item-desc"><b>CAPPUCCINO</b> - espresso, milk, ice</div></div>
        <div class="item"><div class="item-desc"><b>MOCHA</b> - cocoa, milk, ice</div></div>
        <div class="item"><div class="item-desc"><b>STRAWBERRY'S N CREAM</b> - Strawberry, cream, ice</div></div>
        <div class="item"><div class="item-desc"><b>MIGHTY MATCHA</b> - Matcha, cream, ice</div></div>
        <div class="item"><div class="item-note">*Substitute for non dairy for .50p</div></div>
      </div>
      <div class="rule"></div>

      <div class="block">
        <h2 class="section-title">Glee Sandwiches</h2>
        <div class="price-bar">£4.50</div>
        <div class="item"><div class="item-name">Avocado</div><div class="item-desc">Avocado, mozzarella, tomato, pesto</div></div>
        <div class="item"><div class="item-name">Spicy Tuna</div><div class="item-desc">Tuna, chilli peppers, mayo, salt, pepper</div></div>
        <div class="item"><div class="item-name">Tunacado</div><div class="item-desc">Tuna, avocado, mayo, salt, pepper</div></div>
        <div class="item"><div class="item-name">BLT</div><div class="item-desc">Turkey rasher, lettuce, mayo, tomato</div></div>
        <div class="item"><div class="item-name">American Grilled Cheese</div><div class="item-desc">Mature Cheddar, wholewheat bread</div><div class="item-note">*sourdough bread is optional</div></div>
      </div>
      <div class="rule"></div>

      <div class="block">
        <h2 class="section-title">Yogurt</h2>
        <div class="price-bar">£3</div>
        <div class="item"><div class="item-name">Coconut, Vanilla Yogurt, Banana, Granola</div></div>
      </div>
      <div class="rule"></div>

      <div class="block">
        <h2 class="section-title">Bowls</h2>
        <div class="price-bar">£4.50 + Protein=.50p</div>
        <div class="item"><div class="item-name">Acai Bowl</div><div class="item-desc">Acai, raspberry, blueberry, banana, almond milk,<br>granola</div><div class="item-note">*Topping: granola and ½ banana sliced, chia seeds</div></div>
        <div class="item"><div class="item-name">Cocoa Bowl</div><div class="item-desc">Cocoa, banana, peanut butter, almond milk<br>Toppings: chocolate granola, peanut butter, chia<br>seeds, ½ banana sliced</div></div>
      </div>
    </div>
  </div>
</section>

<header class="fascia" aria-label="Shop fascia">
  <span class="fascia-dot" aria-hidden="true"></span>
  <span class="fascia-name">Glee</span>
</header>

<section class="shutter" aria-label="Shutter graphic">
  <div class="shutter-brand">
    <span class="shutter-dot" aria-hidden="true"></span>
    <span class="shutter-name">Glee</span>
  </div>
  <p class="tagline">DRINK HEALTHY<br>EAT HEALTHY</p>
</section>

</body>
</html>
```